Dalvick's Business Card

I need some designs for a new business card including the new logo attached. An old example of our business card is also attached to show all the data that should be included on the new design.
**I added some more examples someone had mocked up**

Contact Information for Business Card

Should include all info on other examples uploaded.

```html
<!DOCTYPE html>
<html lang="en">
<head>
<meta charset="utf-8">
<title>Dalvick's Business Card</title>
<link href="https://fonts.googleapis.com/css2?family=Montserrat:wght@500;600;700&display=swap" rel="stylesheet">
<style>
  :root {
    --bg: #ababab;
    --card-white: #ffffff;
    --brand-blue: #0070b8;
    --brand-red: #e2262e;
    --soft-blue: #a9d0ea;
    --soft-pink: #f7b6b9;
  }
  * { box-sizing: border-box; margin: 0; padding: 0; }
  html, body { width: 1200px; height: 1000px; overflow: hidden; }
  body {
    background: var(--bg);
    font-family: "Montserrat", Arial, sans-serif;
    position: relative;
  }
  .card {
    position: absolute;
    left: 294px;
    width: 613px;
    height: 351px;
    border-radius: 22px;
    overflow: hidden;
  }
  .card-front { top: 92px; background: var(--card-white); }
  .card-back { top: 539px; background: var(--brand-blue); }

  .brand-mark {
    position: absolute;
    display: flex;
    align-items: center;
    gap: 8px;
    font-weight: 700;
  }
  .brand-dot { border-radius: 50%; flex: none; }
  .card-front .brand-mark { left: 48px; top: 74px; color: var(--brand-blue); font-size: 24px; }
  .card-front .brand-dot { width: 20px; height: 20px; background: var(--brand-blue); }

  .front-decor {
    position: absolute;
    right: 0; top: 0;
    width: 270px; height: 351px;
    background: linear-gradient(135deg, var(--soft-pink) 0%, #e8dff0 45%, var(--soft-blue) 100%);
    opacity: 0.55;
    border-top-left-radius: 180px;
    border-bottom-left-radius: 180px;
  }

  .contact { position: absolute; left: 48px; top: 180px; }
  .contact-name { color: var(--brand-blue); font-size: 23px; font-weight: 600; margin-bottom: 12px; }
  .contact-line {
    display: flex; align-items: center; gap: 6px;
    color: var(--brand-red); font-size: 17px; font-weight: 500; line-height: 23px;
  }
  .contact-line svg { width: 11px; height: 11px; fill: var(--brand-blue); flex: none; }

  .card-back .brand-mark {
    left: 0; right: 0; top: 140px;
    justify-content: center;
    color: #fff; font-size: 54px; gap: 16px;
  }
  .card-back .brand-dot { width: 40px; height: 40px; background: #fff; }
  .service-area {
    position: absolute; left: 0; right: 0; top: 311px;
    text-align: center; color: #fff;
    font-size: 13px; font-weight: 600; letter-spacing: 0.3px;
  }
</style>
</head>
<body>
  <section class="card card-front">
    <div class="front-decor" role="img" aria-label="Large faint brand symbol decoration in soft pink and blue"></div>
    <div class="brand-mark"><span class="brand-dot"></span>DALVICK'S</div>
    <div class="contact">
      <p class="contact-name">Ellis Marrow</p>
      <p class="contact-line">
        <svg viewBox="0 0 24 24" aria-hidden="true"><path d="M6.6 10.8a15.1 15.1 0 0 0 6.6 6.6l2.2-2.2c.3-.3.7-.4 1-.2 1.1.4 2.3.6 3.6.6.6 0 1 .4 1 1V20c0 .6-.4 1-1 1A17 17 0 0 1 3 4c0-.6.4-1 1-1h3.5c.6 0 1 .4 1 1 0 1.3.2 2.5.6 3.6.1.3 0 .7-.2 1z"/></svg>
        555.014.2287
      </p>
      <p class="contact-line">
        <svg viewBox="0 0 24 24" aria-hidden="true"><path d="M2 5h20v14H2z M2 5l10 8 10-8" fill="var(--brand-blue)" stroke="#fff" stroke-width="1.5"/></svg>
        hvacdalvick@mailbox.com
      </p>
    </div>
  </section>

  <section class="card card-back">
    <div class="brand-mark"><span class="brand-dot"></span>DALVICK'S</div>
    <p class="service-area">SERVES ALDER CREEK, IA &amp; SURROUNDING AREAS</p>
  </section>
</body>
</html>
```